Landing Page Design for Adult Dating Age Verification (18+)

The objective of this task is to design a visually appealing pre-landing page for the adult dating site "Quillmera (site: https://quillmera.com/)" with an age verification mechanism. The pre-landing page will feature two buttons that redirect visitors to the main offer. The design should also include a footer block that includes links to the terms of use, privacy policy, and contact us pages.

Design Requirements:
Develop an age verification section prominently displayed on the pre-landing page.
Design the section to include two buttons labeled "Yes" and "No" for visitors to confirm their age.
Ensure the section is visually appealing and clearly communicates the purpose of age verification.

Visual Appeal:
Create a visually appealing design that aligns with the branding and theme of the "Quillmera" adult dating site.
Use suitable color schemes, typography, and graphics to enhance the overall visual appeal of the pre-landing page.

Layout and Navigation:
Design an engaging and intuitive layout that encourages visitors to interact with the page and proceed to the main offer.
Ensure clear and visible navigation elements that direct visitors to the main offer or provide additional information.

Responsive Design:
Develop a responsive design that provides a seamless user experience across various devices, including desktop and mobile.
Ensure the design elements and layout adapt well to different screen sizes and resolutions.

File Formats and Assets:
Deliver the final design in PSD, AI, or Sketch format, ensuring that the files are well-organized and layered.
Include any necessary images or assets used in the design, ensuring they are of high quality and optimized for web use.

```html
<!DOCTYPE html>
<html lang="en">
<head>
<meta charset="UTF-8">
<title>Quillmera — Age Verification</title>
<link href="https://fonts.googleapis.com/css2?family=Poppins:wght@400;600;700&family=Playfair+Display:wght@700&display=swap" rel="stylesheet">
<style>
  :root {
    --white: #ffffff;
    --ink: #0b0b0c;
    --brand: #1d1b2a;
    --lilac: #d7b9dc;
    --hero-dark: #2a2420;
    --hero-warm: #5a4a40;
    --modal-bg: rgba(0, 0, 0, 0.72);
    --modal-border: #bdbdbd;
    --yes: #087a0a;
    --footer-band: rgba(170, 140, 175, 0.62);
    --footer-text: #1a1a1a;
  }
  * { box-sizing: border-box; margin: 0; padding: 0; }
  html, body { width: 1200px; height: 844px; overflow: hidden; }
  body { position: relative; font-family: 'Poppins', sans-serif; background: var(--ink); }

  .site-header {
    position: absolute; top: 0; left: 0; width: 1200px; height: 75px;
    background: var(--white);
  }
  .brand {
    position: absolute; left: 116px; top: 17px;
    display: flex; align-items: center; gap: 10px;
  }
  .brand-dot { width: 40px; height: 40px; border-radius: 50%; background: var(--lilac); }
  .brand-name {
    font-family: 'Playfair Display', serif; font-weight: 700;
    font-size: 30px; color: var(--brand); letter-spacing: 0.5px;
  }
  .header-btn {
    position: absolute; top: 16px; width: 139px; height: 47px;
    background: var(--ink); color: var(--white);
    font-weight: 600; font-size: 17px; text-transform: uppercase;
    display: flex; align-items: center; justify-content: center;
    text-decoration: none;
  }
  .header-btn.sign-in { left: 787px; top: 15px; }
  .header-btn.join-now { left: 947px; }

  .hero {
    position: absolute; top: 75px; left: 0; width: 1200px; height: 717px;
    background:
      radial-gradient(ellipse at 55% 35%, rgba(120, 95, 80, 0.55), transparent 60%),
      linear-gradient(110deg, var(--hero-warm) 0%, var(--hero-dark) 45%, #3b302a 75%, #6a6058 100%);
  }
  .hero::after {
    content: ""; position: absolute; inset: 0; background: rgba(0, 0, 0, 0.35);
  }

  .age-gate {
    position: absolute; left: 238px; top: 239px; width: 725px; height: 418px;
    background: var(--modal-bg); border: 2px solid var(--modal-border); border-radius: 7px;
  }
  .age-title {
    position: absolute; left: 0; right: 0; top: 158px; text-align: center;
    color: var(--white); font-weight: 700; font-size: 60px; line-height: 1;
  }
  .age-btn {
    position: absolute; width: 147px; height: 51px;
    border: 2px solid var(--white); color: var(--white);
    font-weight: 700; font-size: 26px;
    display: flex; align-items: center; justify-content: center;
    text-decoration: none;
  }
  .age-btn.yes { left: 206px; top: 280px; background: var(--yes); }
  .age-btn.no { left: 381px; top: 283px; background: var(--ink); }

  .footer-links a {
    position: absolute; top: 733px; color: var(--white);
    font-weight: 600; font-size: 17px; text-decoration: none;
  }
  .footer-links .terms { left: 113px; }
  .footer-links .privacy { left: 520px; }
  .footer-links .contact { right: 114px; top: 735px; }

  .footer-band {
    position: absolute; left: 0; top: 792px; width: 1200px; height: 52px;
    background: var(--footer-band);
    display: flex; align-items: center; justify-content: center;
    color: var(--footer-text); font-size: 13px;
  }
</style>
</head>
<body>
  <header class="site-header">
    <div class="brand">
      <span class="brand-dot"></span>
      <span class="brand-name">Quillmera</span>
    </div>
    <a class="header-btn sign-in" href="https://quillmera.com/">Sign In</a>
    <a class="header-btn join-now" href="https://quillmera.com/">Join Now</a>
  </header>

  <div class="hero" role="img" aria-label="Warm photo of a smiling couple embracing in bed, darkened behind the age check"></div>

  <section class="age-gate">
    <h1 class="age-title">ARE YOU 18+ ?</h1>
    <a class="age-btn yes" href="https://quillmera.com/">YES</a>
    <a class="age-btn no" href="https://quillmera.com/">NO</a>
  </section>

  <nav class="footer-links">
    <a class="terms" href="https://quillmera.com/">Terms of use</a>
    <a class="privacy" href="https://quillmera.com/">Privacy Policy</a>
    <a class="contact" href="https://quillmera.com/">Contact Us</a>
  </nav>

  <footer class="footer-band">© 2023 QUILLMERA. ALL RIGHTS RESERVED.</footer>
</body>
</html>
```